Option Sheet

We need a one page option sheet with a left to right reading of the five options. It should be a one sheet, multiple colors and definitive separations between options This is used in a sales consultation. Backround or colors not in option need to have the follow RGB value (5 red, 20 green, 63 blue)

We added a smaller text file, please change that point

Target Market(s)

Divorce

Industry/Entity Type

Legal

Requirements
Must have
• 1) All five options left to right
• 2)language included in sheet

```html
<!DOCTYPE html>
<html lang="en">
<head>
<meta charset="utf-8">
<title>Five Options – Divorce</title>
<link href="https://fonts.googleapis.com/css2?family=Montserrat:wght@300;600&family=Roboto+Condensed:ital,wght@0,400;0,600;1,400&display=swap" rel="stylesheet">
<style>
  :root {
    --navy: rgb(5, 20, 63);
    --panel: #ffffff;
    --label: #555555;
    --body: #4d4d4d;
    --rule: #e6e6e6;
    --sep: #d4d4d4;
    --opt1: #f0532b;
    --opt2: #d94c98;
    --opt3: #3d3288;
    --opt4: #8cc63f;
    --opt4-alt: #8f80c4;
    --opt5: #17984a;
  }
  * { box-sizing: border-box; margin: 0; padding: 0; }
  html, body { width: 1200px; height: 637px; overflow: hidden; }
  body {
    background: var(--navy);
    font-family: "Roboto Condensed", "Arial Narrow", sans-serif;
    position: relative;
  }
  .sheet-title {
    position: absolute; left: 0; right: 0; text-align: center; color: #fff;
    font-family: "Montserrat", Arial, sans-serif;
  }
  .sheet-title__kicker { top: 31px; font-size: 37px; font-weight: 300; line-height: 46px; }
  .sheet-title__main { top: 80px; font-size: 62px; font-weight: 600; line-height: 70px; letter-spacing: -1px; }

  .options {
    position: absolute; left: 29px; top: 164px; width: 1143px; height: 447px;
    background: var(--panel); border-radius: 4px;
    display: flex; padding-top: 34px;
  }
  .option {
    flex: 1; padding: 0 10px 0 19px; position: relative;
  }
  .option + .option::before {
    content: ""; position: absolute; left: 0; top: 0; width: 1px; height: 384px;
    background: var(--sep);
  }
  .option__number {
    text-align: center; font-style: italic; font-size: 11px; line-height: 13px;
    color: #777; margin-left: -9px;
  }
  .option__name {
    text-align: center; font-weight: 600; font-size: 23px; line-height: 26px;
    letter-spacing: -0.6px; margin: 2px 0 0 -9px; color: var(--accent);
  }
  .option__rule {
    height: 1px; margin: 12px 0 0 -1px; width: 196px;
    background: linear-gradient(90deg, transparent, var(--accent) 50%, transparent);
    opacity: .7;
  }
  .option--1 { --accent: var(--opt1); --box: var(--opt1); }
  .option--2 { --accent: var(--opt2); --box: var(--opt2); }
  .option--3 { --accent: var(--opt3); --box: var(--opt3); }
  .option--4 { --accent: var(--opt4); --box: var(--opt4); }
  .option--4 .pros { --box: var(--opt4-alt); }
  .option--5 { --accent: var(--opt5); --box: var(--opt5); }

  .pros { margin-top: 28px; min-height: 87px; padding-bottom: 25px; border-bottom: 1px solid var(--rule); width: 192px; }
  .cons { margin-top: 21px; }
  .list-heading { font-size: 12px; line-height: 14px; color: #444; font-weight: 400; }
  .items { list-style: none; margin-top: 10px; padding-left: 5px; }
  .items li {
    position: relative; padding-left: 17px; font-style: italic;
    font-size: 11.2px; line-height: 14.4px; color: var(--body);
    letter-spacing: -0.25px; margin-bottom: 9.5px;
  }
  .items li:last-child { margin-bottom: 0; }
  .items li::before {
    content: ""; position: absolute; left: 0; top: 2px; width: 10px; height: 10px;
    border: 1.4px solid var(--box);
  }
</style>
</head>
<body>
  <h1 class="sheet-title sheet-title__kicker">Five Options</h1>
  <h2 class="sheet-title sheet-title__main">DIVORCE</h2>

  <main class="options">
    <section class="option option--1">
      <p class="option__number">option #1</p>
      <h3 class="option__name">Do Nothing</h3>
      <div class="option__rule"></div>
      <div class="pros">
        <h4 class="list-heading">Advantages:</h4>
        <ul class="items"><li>Stay married</li><li>No life Changes</li></ul>
      </div>
      <div class="cons">
        <h4 class="list-heading">Disadvantages:</h4>
        <ul class="items"><li>Remain unhappy, depressed, anxious</li><li>Money and assets may disappear</li><li>What is going to change?</li></ul>
      </div>
    </section>

    <section class="option option--2">
      <p class="option__number">option #2</p>
      <h3 class="option__name">Go to Counseling</h3>
      <div class="option__rule"></div>
      <div class="pros">
        <h4 class="list-heading">Advantages:</h4>
        <ul class="items"><li>Reconcile marriage</li><li>Help make a better life</li></ul>
      </div>
      <div class="cons">
        <h4 class="list-heading">Disadvantages:</h4>
        <ul class="items"><li>Past issues are highlighted and may drudge up old wounds</li><li>It may just clarify the reasons you need to separate and/or divorce</li><li>Both parties must be invested and willing to participate</li></ul>
      </div>
    </section>

    <section class="option option--3">
      <p class="option__number">option #3</p>
      <h3 class="option__name">Do it Yourself</h3>
      <div class="option__rule"></div>
      <div class="pros">
        <h4 class="list-heading">Advantages:</h4>
        <ul class="items"><li>No attorney fees</li><li>You are your own attorney</li></ul>
      </div>
      <div class="cons">
        <h4 class="list-heading">Disadvantages:</h4>
        <ul class="items"><li>People often find that what is “fair,” may in fact, not be truly fair</li><li>Often times, people do not know the risks</li><li>Complicated legal system with intrigue rules</li><li>Unsure how to complete the necessary paperwork and meet the deadlines</li></ul>
      </div>
    </section>

    <section class="option option--4">
      <p class="option__number">option #4</p>
      <h3 class="option__name">Limited Representation</h3>
      <div class="option__rule"></div>
      <div class="pros">
        <h4 class="list-heading">Advantages:</h4>
        <ul class="items"><li>Balance between going alone and our limited involvement in the case</li></ul>
      </div>
      <div class="cons">
        <h4 class="list-heading">Disadvantages:</h4>
        <ul class="items"><li>Our terms may not benefit from our legal knowledge</li><li>The legal consequences of your legal documents will not be explained to you so that you can formulate a plan for handling the rest of your case.</li><li>Your spouse or other parties may cause your legal fees to increase significantly without action on your part</li></ul>
      </div>
    </section>

    <section class="option option--5">
      <p class="option__number">option #5</p>
      <h3 class="option__name">Hire Us</h3>
      <div class="option__rule"></div>
      <div class="pros">
        <h4 class="list-heading">Advantages:</h4>
        <ul class="items"><li>Gain the full benefits of our experience</li><li>Have a team of Family Law focus attorneys</li><li>Often saves you or makes you money in the long run</li><li>Save you time, energy and stress</li></ul>
      </div>
      <div class="cons">
        <h4 class="list-heading">Disadvantages:</h4>
        <ul class="items"><li>Remain unhappy, depressed, anxious</li><li>Money and assets may disappear</li><li>What is going to change?</li></ul>
      </div>
    </section>
  </main>
</body>
</html>
```